Building company buisness cards

We are looking for a sharp modern new look for our business cards.
We are a New Zealand based company that specialises in house and land packages.
We have attached a photo of the current logo and would like to see if it can be improved somehow if needed.
We are open to any colours but we have chosen green at this stage.
Feel free to change the font and make the logo smarter looking.
Play with the colours and see what looks best.

We want a card that looks so good know one will want to throw it away!

Target Market(s)

Home buyers

Industry/Entity Type

Building

Contact Information for Business Card

Derek Tolvane
0217394062
dtolvane@quillmarkhomesteads.co.nz
quillmarkhomesteads.co.nz

Font styles to use
Serif
Sans Serif

Colors

Designer to choose colors to be used in the design.

Requirements
Must have
• Logo and company name on one side, details on the other side
Nice to have
• Color codes for the original green are HEX #4a8028, RGB(74,128,40), CMYK(42,0,69,50)
• Round corners, Raised and/or spot UV

```html
<!DOCTYPE html>
<html lang="en">
<head>
<meta charset="utf-8">
<title>Quillmark Homesteads – Business Cards</title>
<link rel="stylesheet" href="https://fonts.googleapis.com/css2?family=Open+Sans:wght@400;700&display=swap">
<style>
  :root {
    --brand-green: #4a8028;
    --ink-grey: #5a5a5a;
    --soft-grey: #c9c9c9;
    --paper: #ffffff;
    --backdrop: #e4e1de;
    --rule: #bdbdbd;
  }
  * { box-sizing: border-box; margin: 0; padding: 0; }
  html, body {
    width: 1200px;
    height: 997px;
    overflow: hidden;
    background: var(--backdrop);
    font-family: "Open Sans", Arial, sans-serif;
  }
  .card-sheet {
    width: 1200px;
    height: 997px;
    display: flex;
    align-items: center;
    justify-content: center;
    gap: 40px;
  }
  .card {
    position: relative;
    width: 540px;
    height: 310px;
    background: var(--paper);
    border-radius: 10px;
    overflow: hidden;
    box-shadow: 0 2px 6px rgba(0,0,0,0.12);
  }
  .card-waves {
    position: absolute;
    inset: 0;
    width: 100%;
    height: 100%;
  }
  .brand-lockup {
    display: flex;
    align-items: center;
    gap: 10px;
  }
  .brand-mark {
    flex: none;
    background: var(--brand-green);
  }
  .brand-name {
    color: var(--brand-green);
    font-weight: 700;
    line-height: 1.1;
  }
  .brand-name span { display: block; }
  .details-card .brand-lockup {
    position: absolute;
    left: 28px;
    top: 36px;
  }
  .details-card .brand-mark { width: 34px; height: 34px; }
  .details-card .brand-name { font-size: 18px; }
  .holder-name {
    position: absolute;
    right: 34px;
    top: 36px;
    color: var(--brand-green);
    font-weight: 700;
    font-size: 15px;
    line-height: 26px;
  }
  .holder-tab {
    position: absolute;
    right: 0;
    top: 36px;
    width: 12px;
    height: 26px;
    background: var(--brand-green);
  }
  .contact-list {
    position: absolute;
    left: 26px;
    bottom: 26px;
    list-style: none;
    color: var(--paper);
    font-size: 13px;
    line-height: 20px;
  }
  .contact-list li { display: flex; align-items: center; gap: 8px; }
  .contact-list svg { width: 11px; height: 11px; flex: none; }
  .logo-card {
    display: flex;
    align-items: center;
    justify-content: center;
  }
  .logo-card .brand-mark { width: 52px; height: 52px; }
  .logo-card .brand-name { font-size: 28px; }
  .brand-rule {
    position: absolute;
    left: 50%;
    top: 200px;
    width: 70px;
    height: 1px;
    margin-left: -35px;
    background: var(--rule);
  }
</style>
</head>
<body>
<main class="card-sheet">
  <section class="card details-card" aria-label="Business card, contact side">
    <svg class="card-waves" viewBox="0 0 540 310" preserveAspectRatio="none" aria-hidden="true">
      <path d="M0 168 C150 110 320 158 540 72 L540 310 L0 310Z" fill="var(--ink-grey)"/>
      <path d="M0 176 C150 120 320 168 540 84 L540 310 L0 310Z" fill="var(--paper)"/>
      <path d="M0 182 C150 128 320 174 540 92 L540 310 L0 310Z" fill="var(--soft-grey)"/>
      <path d="M0 200 C160 150 330 186 540 104 L540 310 L0 310Z" fill="var(--brand-green)"/>
    </svg>
    <div class="brand-lockup">
      <div class="brand-mark"></div>
      <div class="brand-name"><span>Quillmark</span><span>Homesteads</span></div>
    </div>
    <p class="holder-name">Derek Tolvane</p>
    <div class="holder-tab"></div>
    <ul class="contact-list">
      <li>
        <svg viewBox="0 0 12 12" aria-hidden="true"><path d="M2.5 1 L4.5 1 L5 3.5 L3.8 4.5 C4.5 6 6 7.5 7.5 8.2 L8.5 7 L11 7.5 L11 9.5 C11 10.5 10 11 9 11 C4.5 10.5 1.5 7.5 1 3 C1 2 1.5 1 2.5 1Z" fill="#fff"/></svg>
        0217394062
      </li>
      <li>
        <svg viewBox="0 0 12 12" aria-hidden="true"><rect x="0.5" y="2" width="11" height="8" fill="#fff"/><path d="M0.5 2 L6 6.5 L11.5 2" fill="none" stroke="var(--brand-green)" stroke-width="1"/></svg>
        dtolvane@quillmarkhomesteads.co.nz
      </li>
      <li>
        <svg viewBox="0 0 12 12" aria-hidden="true"><circle cx="6" cy="6" r="5.2" fill="none" stroke="#fff" stroke-width="1.2"/><ellipse cx="6" cy="6" rx="2.2" ry="5.2" fill="none" stroke="#fff" stroke-width="1"/><path d="M0.8 6 H11.2" stroke="#fff" stroke-width="1"/></svg>
        www.quillmarkhomesteads.co.nz
      </li>
    </ul>
  </section>

  <section class="card logo-card" aria-label="Business card, brand side">
    <div class="brand-lockup">
      <div class="brand-mark"></div>
      <div class="brand-name"><span>Quillmark</span><span>Homesteads</span></div>
    </div>
    <div class="brand-rule"></div>
  </section>
</main>
</body>
</html>
```